Bring me business with this creative business card

Design my new business card. I am looking for something different with an impact. People will take a look at this card & they will 1- see how different & creative I am, 2-understand what I do 3- Call me to meet me!

I make videos with a message, testimonials. I am dynamic, fun, creative & human. My new website is in construction but in the meantime you can check this old one: brightpath.ca & another one Tidebloom.com & tidebloom facebook page.
I make videos. sometimes with a cameraman, sometimes with my phone. As an ex Public Relations agent, the message is the most important thing for me. I want to make my clients shine! When they start with me they often remind me of a lamb, when I finish coaching them they are powerful like LIONS! That's why I need a powerful business card!

Target Market(s)

Entrepreneurs, solo entrepreneurs, small & medium companies & start ups. People i will meet while networking. People that need videos on their website & social Networks to get attention, to be visible. men & women. From 35 to 49 years old.
I am an ex Public relations agent. I used to send clients in traditional medias, now with videos they have more chances to be seen on google the new media. I do videos of the president, his team, his loyal clients saying how great the company is & expert videos like series so people can be seen for example every 1 st of every month with a short 2 minute video. Also with my 20 years in marketing & communications I can coach & give tips to anybody who needs it.
Target: anybody who would like my old website brightpath.ca & I also have another website but it will be off line soon: tidebloom.com could give you ideas.

Industry/Entity Type

Communications

Contact Information for Business Card

I am in Montreal,So the business cards have to be the usual size like we have in Montreal: 9 cm x 5 cm
Details:My text: Mathilde Tessier Communication coach/Chief Voice. "Crafting Videos that sound like you" off: 514-555-0147 cell: 514-555-0183. tidebloom.com
mathilde@tidebloom.com logo facebook, youtube, instagram

Colors
f37122

Requirements
Must have
• Dynamic, happy. Orange. Be creative in the look but NOT the shape of the card. Easy to read. Big enough to read.
Should not have
• No funny shapes: no round, no square, just the usual. I love creative but NOT on shape.

```html
<!DOCTYPE html>
<html lang="en">
<head>
<meta charset="utf-8">
<title>Tidebloom business card</title>
<link href="https://fonts.googleapis.com/css2?family=Roboto:wght@400;500&family=Roboto+Condensed:wght@400;500;600&display=swap" rel="stylesheet">
<style>
  :root {
    --backdrop: #262626;
    --card-dark: #1f2021;
    --card-light: #f7f7f5;
    --orange: #f37122;
    --orange-deep: #f05a22;
    --amber: #f7a21b;
    --text-grey: #4a4a4a;
    --rule-light: #e8e8e8;
  }
  * { margin: 0; padding: 0; box-sizing: border-box; }
  html, body { width: 1200px; height: 960px; overflow: hidden; }
  body { background: var(--backdrop); position: relative; font-family: "Roboto", Arial, sans-serif; }

  .card { position: absolute; left: 320px; width: 600px; height: 342px; }
  .card--front { top: 108px; background: var(--card-dark); }
  .card--back { top: 492px; background: var(--card-light); }

  .brand-mark { position: absolute; border-radius: 50%; background: var(--orange); }
  .brand-name {
    position: absolute; font-family: "Roboto Condensed", Arial, sans-serif;
    font-weight: 600; color: var(--orange); letter-spacing: 2px; text-align: center; line-height: 1;
  }
  .brand-line {
    position: absolute; display: flex; align-items: center; justify-content: center; gap: 8px;
    font-family: "Roboto Condensed", Arial, sans-serif; color: var(--amber); text-transform: uppercase; line-height: 1;
  }
  .brand-line::before, .brand-line::after { content: ""; height: 1px; background: var(--amber); }

  /* front */
  .card--front .brand-mark { width: 108px; height: 108px; left: 248px; top: 62px; }
  .card--front .brand-name { left: 0; width: 600px; top: 202px; font-size: 36px; }
  .card--front .brand-line { left: 0; width: 600px; top: 238px; font-size: 15px; }
  .card--front .brand-line::before, .card--front .brand-line::after { width: 30px; }
  .slogan { position: absolute; left: 0; width: 600px; top: 255px; text-align: center; font-size: 14px; line-height: 17px; color: var(--orange); font-weight: 500; }
  .social-row { position: absolute; left: 168px; top: 296px; width: 270px; height: 24px; display: flex; align-items: center; gap: 5px; }
  .social-row .rule { flex: 1; height: 1px; background: linear-gradient(90deg, var(--orange), var(--rule-light)); }
  .social-row .rule:first-child { background: linear-gradient(90deg, var(--rule-light), var(--orange)); }
  .social-dot { width: 22px; height: 22px; border-radius: 50%; background: var(--orange-deep); }
  .social-dot--outline { background: transparent; border: 1.5px solid var(--orange-deep); }

  /* back */
  .card--back .brand-mark { width: 92px; height: 92px; left: 71px; top: 38px; }
  .card--back .brand-name { left: 20px; width: 194px; top: 148px; font-size: 27px; }
  .card--back .brand-line { left: 20px; width: 194px; top: 176px; font-size: 11px; gap: 5px; }
  .card--back .brand-line::before, .card--back .brand-line::after { width: 22px; }

  .person { position: absolute; right: 33px; top: 156px; text-align: right; font-family: "Roboto Condensed", Arial, sans-serif; text-transform: uppercase; }
  .person__name { font-size: 22px; font-weight: 500; color: var(--orange-deep); line-height: 28px; }
  .person__role { font-size: 15px; color: var(--amber); line-height: 19px; }
  .contacts { position: absolute; right: 33px; top: 236px; list-style: none; }
  .contacts li { display: flex; justify-content: flex-end; align-items: center; gap: 7px; font-size: 14px; color: var(--text-grey); line-height: 19.5px; }
  .contacts svg { width: 13px; height: 13px; fill: var(--orange-deep); }
</style>
</head>
<body>

<section class="card card--front">
  <div class="brand-mark" aria-hidden="true"></div>
  <div class="brand-name">TIDEBLOOM</div>
  <div class="brand-line">1 Story&nbsp; 1 Voice</div>
  <p class="slogan">Crafting Videos that sound like you</p>
  <div class="social-row">
    <span class="rule"></span>
    <span class="social-dot"></span>
    <span class="social-dot"></span>
    <span class="social-dot social-dot--outline"></span>
    <span class="rule"></span>
  </div>
</section>

<section class="card card--back">
  <div class="brand-mark" aria-hidden="true"></div>
  <div class="brand-name">TIDEBLOOM</div>
  <div class="brand-line">1 Story&nbsp; 1 Voice</div>

  <div class="person">
    <p class="person__name">Mathilde T.</p>
    <p class="person__role">Communication Coach</p>
    <p class="person__role">Chief Voice</p>
  </div>

  <ul class="contacts">
    <li>514-555-0147
      <svg viewBox="0 0 24 24"><path d="M6.6 10.8a15 15 0 0 0 6.6 6.6l2.2-2.2c.3-.3.7-.4 1-.2 1.1.4 2.3.6 3.6.6.6 0 1 .4 1 1V20c0 .6-.4 1-1 1A17 17 0 0 1 3 4c0-.6.4-1 1-1h3.5c.6 0 1 .4 1 1 0 1.3.2 2.5.6 3.6.1.3 0 .7-.2 1z"/></svg></li>
    <li>514-555-0183
      <svg viewBox="0 0 24 24"><path d="M7 1h10a2 2 0 0 1 2 2v18a2 2 0 0 1-2 2H7a2 2 0 0 1-2-2V3a2 2 0 0 1 2-2zm0 3v14h10V4zm5 15.5a1 1 0 1 0 0 2 1 1 0 0 0 0-2z"/></svg></li>
    <li>mathilde@tidebloom.com
      <svg viewBox="0 0 24 24"><path d="M2 5h20v14H2zm2 2v.5l8 5 8-5V7zm0 3v7h16v-7l-8 5z"/></svg></li>
    <li>www.tidebloom.com
      <svg viewBox="0 0 24 24"><path d="M12 2a10 10 0 1 0 0 20 10 10 0 0 0 0-20zm0 2a8 8 0 0 1 7.4 5h-4.1l-1.8-2.5L11 8.5 8.6 7 6 9.5 7.5 13l3 .5 1 3.5-1 3A8 8 0 0 1 12 4z"/></svg></li>
  </ul>
</section>

</body>
</html>
```